Design Woocommerce & Wordpress Pages and emails

**Freelancer Contest Brief: Transform Steadfast KVL’s Digital Landscape**
**Overview:**
We're thrilled to invite talented designers to participate in a contest aimed at revolutionizing the digital assets of Steadfast KVL, a dynamic leader in the precious metals industry. We are seeking innovative designs for high-converting product pages, engaging product landing pages, transactional emails, versatile marketing email templates, a sophisticated sales funnel, and a redesigned homepage, all seamlessly integrated with WooCommerce and WordPress.
**Project Details:**
1. **Homepage Redesign:**
- **Objective:** Create a balanced homepage that caters to our local audience and our expanding eCommerce market.
- **Requirements:**
- Highlight our dual focus as an eCommerce platform and a local business.
- Emphasize our key services: buying jewelry, selling bullion, and coins.
- Design elements should appeal to both online audiences and local customers, effectively communicating our commitment to serving both communities.
- Deliver the design in Figma to ensure a collaborative and feedback-friendly process.
2. **Product Page Design:**
- **Objective:** Craft a sophisticated and contemporary product page that significantly boosts conversion rates by highlighting product details and fostering trust.
- **Requirements:**
- Include comprehensive product specifications, concise and detailed descriptions, and pricing information.
- Incorporate sections for customer testimonials, trust badges, guarantees, and an engaging "About Us" story.
- Preserve essential information from our existing product pages, while enhancing visual appeal, usability, and most importantly, conversion potential.
- Deliver the design in Figma.
3. **Product Landing Page Design:**
- **Objective:** Develop an impactful landing page to showcase 4-10 products, driving user engagement and interest.
- **Requirements:**
- Present a curated selection of products with striking visuals and succinct descriptions.
- Facilitate easy navigation and encourage exploration of individual product pages.
- Optimize this page for incoming traffic from ads on platforms like Facebook, Instagram, Google, and notably X.com.
4. **Account Page Design:**
- Design a user-friendly and intuitive account page that enhances the customer experience and encourages seamless interaction with our platform.
5. **Transactional Email Design:**
- **Objective:** Develop clear and branded email templates for various order statuses, including processing, completed, canceled, and updated with tracking information.
- **Requirements:** Deliver the email templates in HTML format.
6. **Marketing Email Template Design:**
- **Objective:** Create five versatile marketing email templates, including:
- One template for abandoned cart recovery.
- Four templates for product promotions, designed to quickly adapt to market fluctuations with smart posting features.
- **Requirements:** Ensure templates are flexible and able to accommodate rapid changes in our offerings due to market dynamics. Deliver these in HTML format.
7. **Sales Funnel Design:**
- **Objective:** Design a high-converting sales funnel using PL Chutes and TileSmith, following best funnel practices.
- **Requirements:**
- Focus on a one-product promotion with strategic elements including one order bump, one downsell, and one upsell post-checkout.
- Ensure the funnel is optimized for maximum conversion efficiency and seamlessly integrated within our existing platform.
**Specific Needs:**
- Our current product pages lack effective conversion. We require designs that seamlessly blend elegance with modernity, emphasizing product details while subtly integrating persuasive sales pitches and trust-building elements.
- Email templates must be agile, designed to handle promotional changes driven by fluctuations in the gold and silver markets, with specific products going on sale rapidly.
- The design must allow us to quickly assemble product presentations and efficiently dispatch email campaigns to keep pace with the fast-moving market.
- The homepage redesign should effectively balance the needs of our local store visitors and our online shoppers, emphasizing our services in buying jewelry, and selling bullion and coins.
**References:**
- Current Product Page: [Steadfast KVL Product Page](https://steadfastkvl.example/product/1oz-canadian-gold-maple-leaf-ry/)
- Layout Inspiration: [ClickHarbor Example](https://www.clickharbor.example/call-to-action/mr-bramble-ecommerce-product-page) (Note: We draw inspiration from the layout, not the design style.)
**Submission Guidelines:**
- Submit your designs through ArtHive job board.
- Ensure compatibility with WooCommerce and WordPress platforms.
- Provide product and page designs in Figma and email templates in HTML format.
- Include a brief explanation of your design choices and their alignment with our objectives.
our competitors website Korvin.example, tqingot.example, rfingot.example.
Our website URL: steadfastkvl.example
Target Market(s)
investors, and new investors, hedge against inflation, people needing to sell their gold.
Industry/Entity Type
Precious Metals, ecommerce, we buy gold,

```html
<!DOCTYPE html>
<html lang="en">
<head>
<meta charset="utf-8">
<title>My Account – Steadfast KVL Refiners</title>
<link href="https://fonts.googleapis.com/css2?family=Noto+Sans:wght@400;600;700&display=swap" rel="stylesheet">
<style>
:root{
  --ink:#1b1b1b;
  --muted:#6b6b6b;
  --grey-panel:#eeeeee;
  --rule:#c9c9c9;
  --link:#1f8ab8;
  --ticker-a:#1f5c9e;
  --ticker-b:#0f3f79;
  --down:#e8502a;
  --band-a:#1c5a98;
  --band-b:#0f3c72;
  --footer:#063058;
  --white:#ffffff;
}
*{box-sizing:border-box;margin:0;padding:0}
html,body{width:817px;height:1200px;overflow:hidden}
body{font-family:"Noto Sans",sans-serif;color:var(--ink);background:var(--white);position:relative}
a{color:inherit;text-decoration:none}
.abs{position:absolute}

.ticker{left:0;top:0;width:817px;height:28px;background:linear-gradient(180deg,var(--ticker-a),var(--ticker-b));color:var(--white);font-size:8px;display:flex;align-items:center;justify-content:space-between;padding:0 17px}
.ticker b{font-weight:600}
.ticker .chg{color:var(--down)}
.ticker .tri{display:inline-block;width:0;height:0;border-left:3.5px solid transparent;border-right:3.5px solid transparent;border-top:4px solid var(--down);margin:0 4px 0 5px;vertical-align:1px}

.brand{display:flex;align-items:center;gap:8px;font-size:10.5px;font-weight:400;letter-spacing:.2px;color:var(--ink)}
.brand .mark{width:14px;height:14px;border-radius:50%;background:currentColor}
.header-brand{left:77px;top:53px}
.search{left:360px;top:48px;width:210px;height:29px;border:1px solid var(--rule);display:flex;align-items:center;justify-content:space-between;padding:0 9px;font-size:8.5px;color:#8a8a8a}
.account-links{left:609px;top:54px;display:flex;gap:18px;font-size:11.5px;font-weight:600;align-items:center}
.account-links span{display:flex;align-items:center;gap:5px}

.nav{left:0;top:96px;width:817px;height:29px;background:var(--grey-panel);font-size:9px}
.nav ul{list-style:none;position:relative;height:100%}
.nav li{position:absolute;top:0;height:29px;line-height:29px}
.nav .sep{position:absolute;top:0;width:1px;height:29px;background:var(--white)}

.page-title{left:77px;top:152px;font-size:26px;font-weight:700;color:var(--muted)}

.sidebar{left:77px;top:201px;width:153px;height:267px;background:var(--grey-panel);padding:14px 14px 0}
.sidebar h2{font-size:13.5px;font-weight:600;padding-bottom:9px;border-bottom:1px solid var(--rule)}
.sidebar ul{list-style:none;font-size:9px;padding:7px 0 6px;border-bottom:1px solid var(--rule)}
.sidebar ul:last-child{border-bottom:none}
.sidebar li{line-height:18.5px}
.sidebar .current{color:var(--link);text-decoration:underline}

.section-head{left:247px;width:494px;border-bottom:1px solid var(--rule);display:flex;justify-content:space-between;align-items:flex-end;padding:0 3px 9px}
.section-head h3{font-size:14px;font-weight:700}
.section-head a{font-size:9px}

.card{background:var(--grey-panel)}
.contact{left:247px;top:244px;width:266px;height:131px}
.avatar{position:absolute;left:18px;top:18px;width:47px;height:47px;border-radius:50%;background:#d6d6d6;display:flex;align-items:center;justify-content:center}
.contact .body{position:absolute;left:75px;top:18px;font-size:9px}
.card h4{font-size:11.5px;font-weight:700;margin-bottom:6px}
.edit{color:var(--muted);font-size:9px;display:flex;align-items:center;gap:4px}
.addr{top:435px;width:238px;height:93px;padding:18px 21px}
.addr p{font-size:9px;margin-bottom:12px}

.band{left:0;top:594px;width:817px;height:77px;background:linear-gradient(180deg,var(--band-a),var(--band-b));color:var(--white)}
.band .item{position:absolute;top:17px;display:flex;gap:11px}
.band .icon{width:40px;height:40px;border:1px solid var(--white);display:flex;align-items:center;justify-content:center;flex:none}
.band .label{font-size:8.5px;opacity:.85;margin-top:1px}
.band .value{font-size:13.5px;font-weight:700;line-height:19px;margin-top:3px}

.footer{left:0;top:671px;width:817px;height:529px;background:var(--footer);color:var(--white)}
.col{position:absolute;top:57px}
.col h5{font-size:11.5px;font-weight:700;letter-spacing:.3px;line-height:15.5px;margin-bottom:12px}
.col ul{list-style:none;font-size:9px}
.col li{line-height:22.7px}
.col p{font-size:8.6px;line-height:13.6px;width:150px}
.symbols{display:flex;gap:24px;margin-top:9px;align-items:center}
.footer .rule{position:absolute;left:77px;top:350px;width:663px;height:1px;background:rgba(255,255,255,.2)}
.footer .brand{position:absolute;left:0;width:817px;top:386px;justify-content:center;color:var(--white);font-size:14px}
.footer .brand .mark{width:18px;height:18px}
.socials{position:absolute;top:425px;left:0;width:817px;display:flex;justify-content:center;gap:7px}
.socials span{width:21px;height:21px;border-radius:50%;background:var(--white);display:flex;align-items:center;justify-content:center}
.socials span i{width:7px;height:7px;border-radius:50%;background:var(--footer)}
.copy{position:absolute;top:466px;width:817px;text-align:center;font-size:8.5px}
</style>
</head>
<body>

<div class="abs ticker">
  <span><b>GOLD</b> $2,739.29<i class="tri"></i><span class="chg">($27.40) -0.99%</span></span>
  <span><b>SILVER</b> $33.91<i class="tri"></i><span class="chg">($1.24) -3.52%</span></span>
  <span><b>PLATINUM</b> $1,025.75<i class="tri"></i><span class="chg">($14.00) -1.34%</span></span>
  <span><b>PALLADIUM</b> $1,085.44<i class="tri"></i><span class="chg">($18.40) -1.71%</span></span>
</div>

<div class="abs brand header-brand"><span class="mark"></span>STEADFAST KVL REFINERS</div>

<div class="abs search">Search
  <svg width="12" height="12" viewBox="0 0 12 12" fill="none" stroke="#1f8ab8" stroke-width="1.2"><circle cx="5" cy="5" r="4"/><path d="M8 8l3 3"/></svg>
</div>

<div class="abs account-links">
  <span><svg width="11" height="12" viewBox="0 0 11 12" fill="none" stroke="#1f6fb0" stroke-width="1.2"><circle cx="5.5" cy="3.5" r="2.8"/><path d="M1 11.5c0-3 2-4.5 4.5-4.5S10 8.5 10 11.5"/></svg>Sign In</span>
  <span><svg width="10" height="12" viewBox="0 0 10 12" fill="none" stroke="#1f6fb0" stroke-width="1.2"><rect x="1" y="3.5" width="8" height="8"/><path d="M3 3.5V2a2 2 0 014 0v1.5"/></svg>Cart: (0)</span>
</div>

<nav class="abs nav">
  <ul>
    <li style="left:77px">GOLD</li><i class="sep" style="left:132px"></i>
    <li style="left:161px">SILVER</li><i class="sep" style="left:219px"></i>
    <li style="left:248px">SHOP ALL</li><i class="sep" style="left:319px"></i>
    <li style="left:348px">DEALS</li><i class="sep" style="left:405px"></i>
    <li style="left:434px">SELL TO US</li><i class="sep" style="left:511px"></i>
    <li style="left:540px">WE BUY</li><i class="sep" style="left:603px"></i>
    <li style="left:632px">IRA</li><i class="sep" style="left:676px"></i>
    <li style="left:703px">JEWELRY</li>
  </ul>
</nav>

<h1 class="abs page-title">My Account</h1>

<aside class="abs sidebar">
  <h2>My Account</h2>
  <ul><li class="current">Dashboard</li><li>My Orders</li><li>My Wish List</li></ul>
  <ul><li>Address Book</li><li>Account Information</li><li>Store Credit</li></ul>
  <ul><li>Credit Cards</li><li>Bank Account</li></ul>
  <ul><li>Logout</li></ul>
</aside>

<div class="abs section-head" style="top:201px"><h3>Account Information</h3></div>

<div class="abs card contact">
  <div class="avatar"><svg width="18" height="19" viewBox="0 0 18 19" fill="none" stroke="#1f8ab8" stroke-width="1.5"><circle cx="9" cy="5.5" r="4.5"/><path d="M1.5 18.5c0-4.5 3.3-7 7.5-7s7.5 2.5 7.5 7"/></svg></div>
  <div class="body">
    <h4>Contact Information</h4>
    <div>Jordan Vale</div>
    <div style="margin-top:16px">jordan.vale@mailbox.example</div>
    <div class="edit" style="margin-top:5px">Edit <svg width="7" height="7" viewBox="0 0 7 7" fill="none" stroke="#6b6b6b"><path d="M1 6l.5-2L5 .5 6.5 2 3 5.5z"/></svg></div>
    <div class="edit" style="margin-top:6px">Change Password <span style="margin-left:6px">›</span></div>
  </div>
</div>

<div class="abs section-head" style="top:396px"><h3>Address Book</h3><a href="#">Manage Addresses</a></div>

<div class="abs card addr" style="left:247px">
  <h4>Default Billing Address</h4>
  <p>You have not set a default billing address.</p>
  <div class="edit">Edit <svg width="7" height="7" viewBox="0 0 7 7" fill="none" stroke="#6b6b6b"><path d="M1 6l.5-2L5 .5 6.5 2 3 5.5z"/></svg></div>
</div>
<div class="abs card addr" style="left:502px">
  <h4>Default Shipping Address</h4>
  <p>You have not set a default shipping address.</p>
  <div class="edit">Edit <svg width="7" height="7" viewBox="0 0 7 7" fill="none" stroke="#6b6b6b"><path d="M1 6l.5-2L5 .5 6.5 2 3 5.5z"/></svg></div>
</div>

<section class="abs band">
  <div class="item" style="left:77px">
    <div class="icon"><svg width="18" height="18" viewBox="0 0 18 18" fill="none" stroke="#fff" stroke-width="1.3"><path d="M3 1.5l3 .5 1 4-2 1.5c1 2.5 3 4.5 5.5 5.5l1.5-2 4 1 .5 3c-.5 1-1.5 1.5-2.5 1.5C7.5 16.5 1.5 10.5 1.5 4 1.5 3 2 2 3 1.5z"/></svg></div>
    <div><div class="label">CALL US</div><div class="value">(555) 014-2271</div></div>
  </div>
  <div class="item" style="left:267px">
    <div class="icon"><svg width="20" height="15" viewBox="0 0 20 15" fill="none" stroke="#fff" stroke-width="1.3"><rect x="1" y="1" width="18" height="13" rx="1"/><path d="M1 2l9 7 9-7"/></svg></div>
    <div><div class="label">EMAIL US</div><div class="value">info@steadfastkvl.example</div></div>
  </div>
  <div class="item" style="left:523px">
    <div class="icon"><svg width="16" height="19" viewBox="0 0 16 19" fill="none" stroke="#fff" stroke-width="1.3"><path d="M8 18s6.5-6 6.5-10.5a6.5 6.5 0 00-13 0C1.5 12 8 18 8 18z"/><circle cx="8" cy="7.5" r="2.5"/></svg></div>
    <div><div class="label">ADDRESS</div><div class="value">4120 Larchmont Way NE,<br>Riverton, OR 97000</div></div>
  </div>
</section>

<footer class="abs footer">
  <div class="col" style="left:77px"><h5>BUYING &amp; SELLING</h5>
    <ul><li>Shop Bullion</li><li>IRA Rollovers</li><li>Silver Bullion</li><li>Gold Bullion</li><li>Platinum Bullion</li><li>Palladium Bullion</li><li>Steadfast Jewelry</li></ul></div>
  <div class="col" style="left:218px"><h5>COMPANY</h5>
    <ul><li>Leave a Review</li><li>Testimonials</li><li>Refinery Process</li><li>Blog</li><li>About Us</li></ul></div>
  <div class="col" style="left:326px"><h5>CUSTOMER CARE</h5>
    <ul><li>My account</li><li>Investment Tools</li><li>Contact us</li><li>FAQs</li><li>Jewelry 101</li><li>Jewelry Repair</li></ul></div>
  <div class="col" style="left:456px"><h5>LEGAL</h5>
    <ul><li>Privacy Policy</li><li>Terms and Conditions</li><li>Mail-in Terms</li><li>Acceptable Use</li><li>Cookie Policy</li><li>Disclaimer Policy</li><li>Payment Terms</li><li>Shipping Policy</li><li>Returns Policy</li><li>Price Match</li></ul></div>
  <div class="col" style="left:593px"><h5>OPEN MON-FRI<br>10:00AM - 6:00PM PST</h5>
    <p>Steadfast KVL Refiners is a proudly patriotic Christian business in the United States of America.</p>
    <div class="symbols">
      <div role="img" aria-label="Cross symbol" style="width:18px;height:26px;background:#ffffff"></div>
      <div role="img" aria-label="Waving American flag" style="width:52px;height:24px;background:linear-gradient(90deg,#3a56b0 0 35%,#e84040 35%)"></div>
    </div>
  </div>
  <div class="rule"></div>
  <div class="brand"><span class="mark"></span>STEADFAST KVL REFINERS</div>
  <div class="socials"><span><i></i></span><span><i></i></span><span><i></i></span><span><i></i></span><span><i></i></span></div>
  <div class="copy">© 2024 All Rights Reserved Steadfast KVL Refiners</div>
</footer>

</body>
</html>
```